Real Estate Company / Capital Needs Cards!

need business cards designed using the logos that were just designed by pixelbarn.

Reason: per designers request deadline extended 1 day…thank you.

Target Market(s)

Investors and clients looking to purchase real estate or invest in the business.

Industry/Entity Type

Business

Requirements
Must have
• two designs - one for the real estate logo and one for the capital logo, similar but slightly different.
Nice to have
• something to make it pop (perhaps on the back)
Should not have
• much color

```html
<!DOCTYPE html>
<html lang="en">
<head>
<meta charset="utf-8">
<title>Halden Real Estate – Business Cards</title>
<link rel="stylesheet" href="https://fonts.googleapis.com/css2?family=Libre+Baskerville:wght@400;700&family=PT+Sans:wght@400;700&display=swap">
<style>
  :root {
    --page-bg: #ece9e6;
    --card-bg: #ffffff;
    --ink-dark: #4a4a4c;
    --ink-mid: #6b6b6e;
    --logo-grey: #7d7d80;
    --band-dark: #6d6d70;
    --band-light: #b9b9bc;
    --divider: #c8c8ca;
    --text-white: #ffffff;
  }
  * { box-sizing: border-box; margin: 0; padding: 0; }
  html, body { width: 1200px; height: 498px; overflow: hidden; }
  body {
    background: var(--page-bg);
    position: relative;
    font-family: "PT Sans", Arial, sans-serif;
    color: var(--ink-dark);
  }
  .card {
    position: absolute;
    top: 99px;
    width: 520px;
    height: 300px;
    background: var(--card-bg);
    border-radius: 24px;
    overflow: hidden;
    box-shadow: 0 4px 14px rgba(0,0,0,0.18);
  }
  .card--front { left: 45px; }
  .card--back { left: 635px; }

  /* logo stand-in: name set in text font plus one plain square */
  .brand { position: absolute; display: flex; align-items: center; }
  .brand__square { background: var(--logo-grey); flex: none; }
  .brand__name {
    font-family: "Libre Baskerville", Georgia, serif;
    font-weight: 400;
    color: var(--logo-grey);
    line-height: 1;
  }
  .brand__main { display: block; letter-spacing: 0.04em; }
  .brand__sub { display: block; letter-spacing: 0.18em; }

  .card--front .brand { left: 30px; top: 88px; }
  .card--front .brand__square { width: 44px; height: 52px; margin-right: 10px; }
  .card--front .brand__main { font-size: 30px; }
  .card--front .brand__sub { font-size: 11px; margin-top: 4px; }

  .divider {
    position: absolute;
    left: 238px; top: 22px;
    width: 1px; height: 160px;
    background: var(--divider);
  }
  .contact { position: absolute; left: 255px; top: 22px; }
  .contact__name {
    font-family: "Libre Baskerville", Georgia, serif;
    font-weight: 700;
    font-size: 15px;
    letter-spacing: 0.02em;
  }
  .contact__title {
    font-family: "Libre Baskerville", Georgia, serif;
    font-size: 13px;
    color: var(--ink-mid);
    margin: 2px 0 6px;
  }
  .contact__line { display: flex; align-items: center; font-size: 15px; margin-bottom: 5px; }
  .contact__line--small { font-size: 13px; }
  .contact__icon { width: 12px; height: 12px; margin-right: 4px; fill: var(--ink-dark); }
  .contact__address { font-size: 13.5px; line-height: 1.35; margin-top: 16px; padding-left: 16px; }

  .bands { position: absolute; left: 0; top: 0; width: 520px; height: 300px; }
  .band-url {
    position: absolute;
    right: 20px; top: 212px;
    font-size: 15px;
    color: var(--text-white);
    letter-spacing: 0.08em;
  }
  .band-url b { font-weight: 700; }

  .card--back .brand { left: 78px; top: 66px; }
  .card--back .brand__square { width: 90px; height: 110px; margin-right: 16px; }
  .card--back .brand__main { font-size: 56px; }
  .card--back .brand__sub { font-size: 20px; margin-top: 6px; letter-spacing: 0.16em; }
  .back-url {
    position: absolute;
    left: 0; right: 0; top: 212px;
    text-align: center;
    font-size: 16px;
    letter-spacing: 0.14em;
    color: var(--ink-dark);
  }
  .back-url b { font-weight: 700; }
</style>
</head>
<body>
  <section class="card card--front" aria-label="Business card front">
    <svg class="bands" viewBox="0 0 520 300" aria-hidden="true">
      <rect x="0" y="252" width="520" height="48" fill="var(--band-light)"/>
      <polygon points="250,202 520,202 520,300 300,300 300,252 282,252" fill="var(--band-dark)"/>
    </svg>

    <div class="brand">
      <span class="brand__square"></span>
      <span class="brand__name">
        <span class="brand__main">HALDEN</span>
        <span class="brand__sub">REAL ESTATE</span>
      </span>
    </div>

    <div class="divider"></div>

    <div class="contact">
      <p class="contact__name">YOUR NAME</p>
      <p class="contact__title">Title</p>
      <p class="contact__line">
        <svg class="contact__icon" viewBox="0 0 12 12"><path d="M2.5 1l2 2.2-1 1.3c.7 1.5 1.8 2.6 3.3 3.3l1.3-1 2.2 2-1.2 1.8C5.5 10.4 1.6 6.5 1 2.2z"/></svg>
        555-014-7980
      </p>
      <p class="contact__line">
        <svg class="contact__icon" viewBox="0 0 12 12"><rect x="3" y="1" width="6" height="3"/><rect x="1" y="4.5" width="10" height="5" rx="1"/><rect x="3" y="8" width="6" height="3"/></svg>
        555-016-7896
      </p>
      <p class="contact__line contact__line--small">
        <svg class="contact__icon" viewBox="0 0 12 12"><path d="M1 3h10v7H1z M1 3l5 4 5-4" fill="none" stroke="var(--ink-dark)" stroke-width="1.4"/></svg>
        hello@haldenrealestate.com
      </p>
      <p class="contact__address">Street Name, City Name<br>State ZipCode</p>
    </div>

    <p class="band-url">www.<b>haldenrealestate</b>.com</p>
  </section>

  <section class="card card--back" aria-label="Business card back">
    <div class="brand">
      <span class="brand__square"></span>
      <span class="brand__name">
        <span class="brand__main">HALDEN</span>
        <span class="brand__sub">REAL ESTATE</span>
      </span>
    </div>
    <p class="back-url">www.<b>haldenrealestate</b>.com</p>
  </section>
</body>
</html>
```